business card deign

Logo needs the following on it.
1. attached logo
2. Tagline - "If it keeps a drink cold or the party going...we do it!"
3. Name- Dalton Pikes, Founder and CPO
4. Address - 412 E. Carver Avenue, Ste 2207, Tampa, FL. 33917
5. Phone - 555.318.4726

```html
<!DOCTYPE html>
<html lang="en">
<head>
<meta charset="utf-8">
<title>Kelvo Business Card</title>
<link href="https://fonts.googleapis.com/css2?family=Roboto:wght@400;700&display=swap" rel="stylesheet">
<style>
  :root {
    --stage: #222222;
    --ink: #0b0b0b;
    --paper: #ffffff;
    --card-dark: #0f0f0f;
    --muted: #1c1c1c;
  }
  * { margin: 0; padding: 0; box-sizing: border-box; }
  html, body { width: 1200px; height: 711px; overflow: hidden; background: var(--stage); }
  body { position: relative; font-family: "Roboto", Arial, sans-serif; }

  .card {
    position: absolute;
    top: 207px;
    width: 520px;
    height: 297px;
    border-radius: 18px;
    overflow: hidden;
  }
  .card--front { left: 50px; background: var(--card-dark); }
  .card--back { left: 630px; background: var(--paper); color: var(--ink); }

  .brand {
    position: absolute;
    display: flex;
    align-items: center;
    gap: 12px;
    font-weight: 700;
    letter-spacing: 10px;
  }
  .brand__mark { width: 18px; height: 18px; }
  .card--front .brand {
    left: 50%; top: 50%;
    transform: translate(-50%, -50%);
    color: var(--paper);
    font-size: 42px;
  }
  .card--front .brand__mark { background: var(--paper); }
  .card--back .brand {
    left: 34px; top: 100px;
    color: var(--ink);
    font-size: 30px;
    letter-spacing: 7px;
  }
  .card--back .brand__mark { background: var(--ink); width: 14px; height: 14px; }

  .divider {
    position: absolute;
    left: 256px; top: 48px;
    width: 1px; height: 150px;
    background: var(--ink);
  }

  .details { position: absolute; left: 282px; top: 42px; width: 230px; }
  .details__name { font-size: 24px; font-weight: 700; line-height: 1.1; }
  .details__role { font-size: 13px; margin-top: 3px; }
  .details__tagline { font-size: 11px; line-height: 1.4; margin-top: 10px; }
  .contact { list-style: none; margin-top: 12px; font-size: 11px; line-height: 1.4; }
  .contact__item { display: flex; gap: 7px; align-items: flex-start; margin-bottom: 3px; }
  .contact__icon { width: 11px; height: 11px; flex: none; margin-top: 2px; }

  .stripes { position: absolute; left: 0; bottom: 0; width: 520px; height: 110px; }
</style>
</head>
<body>
  <section class="card card--front" aria-label="Card front">
    <div class="brand"><span class="brand__mark"></span><span class="brand__name">KELVO</span></div>
  </section>

  <section class="card card--back" aria-label="Card back">
    <div class="brand"><span class="brand__mark"></span><span class="brand__name">KELVO</span></div>

    <div class="divider"></div>

    <div class="details">
      <h1 class="details__name">Dalton Pikes</h1>
      <p class="details__role">Founder and CPO</p>
      <p class="details__tagline">If it keeps a drink cold or<br>the party going...we do it!</p>
      <ul class="contact">
        <li class="contact__item">
          <svg class="contact__icon" viewBox="0 0 24 24"><path fill="#0b0b0b" d="M6.6 10.8a15 15 0 0 0 6.6 6.6l2.2-2.2c.3-.3.7-.4 1-.2 1.1.4 2.3.6 3.6.6.6 0 1 .4 1 1V20c0 .6-.4 1-1 1A17 17 0 0 1 3 4c0-.6.4-1 1-1h3.5c.6 0 1 .4 1 1 0 1.3.2 2.5.6 3.6.1.3 0 .7-.2 1z"/></svg>
          <span>555.318.4726</span>
        </li>
        <li class="contact__item">
          <svg class="contact__icon" viewBox="0 0 24 24"><path fill="#0b0b0b" d="M12 2a7 7 0 0 0-7 7c0 5 7 13 7 13s7-8 7-13a7 7 0 0 0-7-7zm0 9.5A2.5 2.5 0 1 1 12 6.5a2.5 2.5 0 0 1 0 5z"/></svg>
          <span>412 E. Carver Avenue,<br>Ste 2207, Tampa, FL. 33917</span>
        </li>
      </ul>
    </div>

    <svg class="stripes" viewBox="0 0 520 110" preserveAspectRatio="none" aria-hidden="true">
      <path fill="#0b0b0b" d="M0 86 H520 V98 H0 Z"/>
      <path fill="#0b0b0b" d="M0 70 H240 Q250 70 262 60 L282 44 H520 V54 H298 Q288 54 278 62 L262 76 Q254 82 244 82 H0 Z"/>
      <path fill="#0b0b0b" d="M286 44 L520 0 V14 L300 56 Z"/>
    </svg>
  </section>
</body>
</html>
```